Timber Crest Construction Needs business card

Hey we are in need of business card designs. I have upload our logo as a guideline, but free feel to run with it or come up with something unique.
Pls have fun with it and be creative. the name says it all!
i will give some directions after i see a few entries..
Updates
Logo source file has been uploaded..
Hey because of the logo is so colourful already.
Can we have a few submissions with less colour.
Also we are looking for clever/hidden/descriptive business card.

```html
<!DOCTYPE html>
<html lang="en">
<head>
<meta charset="utf-8">
<title>Timber Crest Construction – Business Card</title>
<link rel="stylesheet" href="https://fonts.googleapis.com/css2?family=Questrial&family=Arimo:wght@400;700&display=swap">
<style>
  :root {
    --stage: #c9c9c9;
    --stage-light: #e6e6e6;
    --card: #ffffff;
    --brand-grey: #7a7a7c;
    --ink: #1d1d1d;
    --accent-red: #e3202a;
    --accent-green: #1a9a48;
    --accent-blue: #1f7fc8;
    --accent-yellow: #f3d21b;
    --accent-black: #2b2b2b;
    --bar-grey: #d4d4d4;
  }
  * { box-sizing: border-box; margin: 0; padding: 0; }
  html, body { width: 1200px; height: 960px; overflow: hidden; }
  body {
    position: relative;
    background: radial-gradient(ellipse at 45% 55%, var(--stage-light) 0%, var(--stage) 75%);
    font-family: "Arimo", Arial, sans-serif;
  }
  .card {
    position: absolute;
    width: 650px;
    height: 390px;
    background: var(--card);
    box-shadow: 0 4px 14px rgba(0,0,0,.28);
    overflow: hidden;
  }
  .card--front { left: 60px; top: 60px; }
  .card--back  { left: 400px; top: 420px; }

  .colour-band {
    position: absolute;
    left: 18px; right: 18px; bottom: 16px;
    height: 11px;
    background: linear-gradient(90deg,
      var(--accent-black), var(--accent-red), var(--accent-green),
      var(--accent-blue), var(--accent-yellow), var(--accent-red),
      var(--accent-blue), var(--accent-green), var(--accent-black));
  }

  .brand-name {
    font-family: "Questrial", "Century Gothic", sans-serif;
    font-weight: 400;
    color: var(--brand-grey);
    text-transform: uppercase;
    line-height: 1;
    white-space: nowrap;
  }
  .card--front .brand {
    position: absolute;
    left: 0; right: 0; top: 150px;
    text-align: center;
  }
  .card--front .brand-name { font-size: 64px; letter-spacing: 1px; }
  .card--front .brand-sub  { font-size: 22px; letter-spacing: 3px; margin-top: 8px; }
  .brand-square {
    display: block;
    width: 34px; height: 34px;
    margin: 0 auto 22px;
    background: var(--brand-grey);
  }

  .name-tab {
    position: absolute;
    left: 28px; top: 48px;
    background: var(--accent-red);
    color: #fff;
    font-size: 13px;
    font-variant: small-caps;
    letter-spacing: .5px;
    padding: 3px 30px 3px 28px;
  }
  .card--back .brand {
    position: absolute;
    right: 40px; top: 82px;
    text-align: right;
  }
  .card--back .brand-name { font-size: 34px; }
  .card--back .brand-sub  { font-size: 13px; letter-spacing: 2px; margin-top: 4px; }

  .tower-backdrop {
    position: absolute;
    left: 325px; right: 40px; top: 150px; bottom: 34px;
    background: linear-gradient(180deg, var(--bar-grey) 0%, #ececec 100%);
  }

  .contact {
    position: absolute;
    left: 38px; top: 240px;
    list-style: none;
    font-size: 14px;
    color: var(--ink);
  }
  .contact li { display: flex; align-items: center; gap: 10px; height: 24px; }
  .contact .web { font-size: 11px; letter-spacing: .5px; }
  .contact-icon {
    width: 16px; height: 16px;
    background: var(--accent-red);
    display: flex; align-items: center; justify-content: center;
  }
</style>
</head>
<body>

<section class="card card--front">
  <div class="brand">
    <span class="brand-square"></span>
    <div class="brand-name">Timber Crest</div>
    <div class="brand-name brand-sub">Construction</div>
  </div>
  <div class="colour-band" role="img" aria-label="Row of small coloured blocks"></div>
</section>

<section class="card card--back">
  <div class="name-tab">Name Surname</div>
  <div class="tower-backdrop" role="img" aria-label="Decorative vertical grey columns"></div>
  <div class="brand">
    <div class="brand-name">Timber Crest</div>
    <div class="brand-name brand-sub">Construction</div>
  </div>
  <ul class="contact">
    <li>
      <span class="contact-icon">
        <svg width="10" height="12" viewBox="0 0 10 12"><rect x="2" y="1" width="6" height="10" rx="1" fill="none" stroke="#fff" stroke-width="1.4"/></svg>
      </span>55 555 55555
    </li>
    <li>
      <span class="contact-icon">
        <svg width="12" height="10" viewBox="0 0 12 10"><rect x="1" y="3" width="10" height="6" fill="none" stroke="#fff" stroke-width="1.4"/><rect x="3" y="1" width="6" height="2" fill="#fff"/></svg>
      </span>44 4444 4444
    </li>
    <li>
      <span class="contact-icon">
        <svg width="12" height="10" viewBox="0 0 12 10"><rect x="1" y="1.5" width="10" height="7" fill="none" stroke="#fff" stroke-width="1.3"/><path d="M1 1.5 L6 6 L11 1.5" fill="none" stroke="#fff" stroke-width="1.3"/></svg>
      </span>info@timbercrestbuild.com
    </li>
    <li class="web">
      <span class="contact-icon">
        <svg width="12" height="12" viewBox="0 0 12 12"><circle cx="6" cy="6" r="4.5" fill="none" stroke="#fff" stroke-width="1.2"/><path d="M1.5 6 H10.5 M6 1.5 V10.5" stroke="#fff" stroke-width="1"/></svg>
      </span>WWW.TIMBERCRESTBUILD.COM
    </li>
  </ul>
  <div class="colour-band" role="img" aria-label="Row of small coloured blocks"></div>
</section>

</body>
</html>
```